Australian Trucking Company Requires Professional Looking Stationary

We require a professional looking stationary design that incorporates our newly designed logo.

Our business, called "Brell Haulage Contracting", provides contracting work, transport and logistics to business in Western Australia particularly with links to the mining sector.

We are a small business looking to expand and our new logo and our new stationary will help develop our brand image in our market place.

Target Market(s)

Businesses and Corporation with links to the Mining Sector

Industry/Entity Type

Small Business

Requirements
Must have
• The letterhead must have the following details:
The new logo

Text saying: "Brell Holdings Pty Ltd (ACN 582 316 907) ATF The Brell Discretionary Trust T/AS"
"ABN 71 834 209 553"
Address "P.O Box 817 Wattlegrove WA, 6958"
Phone: 08 9352 7140
Email: brellhaul@mailbox-example.com.au

The text on the letterhead should be editable as the details are likely to change in the near future. Provision should be made for a website address all though one isn't available at the moment.

The styling, layout and font text is entirely up to the designer.

```html
<!DOCTYPE html>
<html lang="en">
<head>
<meta charset="utf-8">
<title>Brell Haulage Contracting – Business Cards</title>
<link rel="stylesheet" href="https://fonts.googleapis.com/css2?family=Arimo:wght@400;700&display=swap">
<style>
  :root {
    --page-bg: #ece9e4;
    --card-bg: #ffffff;
    --brand-red: #b0141c;
    --deep-red: #7a0008;
    --bright-red: #e01b24;
    --text-dark: #333333;
    --text-grey: #6b6b6b;
    --mark-grey: #6f6f6f;
    --silver: #c9c9c9;
  }
  * { margin: 0; padding: 0; box-sizing: border-box; }
  html, body { width: 1200px; height: 1200px; overflow: hidden; }
  body {
    background: var(--page-bg);
    font-family: "Arimo", Arial, sans-serif;
    position: relative;
  }
  .card {
    position: absolute;
    background: var(--card-bg);
    border-radius: 28px;
    overflow: hidden;
    box-shadow: 0 4px 14px rgba(0,0,0,0.18);
  }
  .card-front { left: 84px; top: 80px; width: 840px; height: 482px; }
  .card-back { left: 290px; top: 648px; width: 838px; height: 478px; }

  .brand-square {
    position: absolute; left: 120px; top: 60px;
    width: 120px; height: 120px;
    background: var(--mark-grey);
  }
  .brand-name {
    position: absolute; left: 296px; top: 34px;
    color: var(--brand-red);
    font-weight: 700; font-size: 56px; line-height: 58px;
    text-transform: uppercase;
  }

  .contact-list { position: absolute; left: 136px; top: 222px; list-style: none; }
  .contact-list li {
    display: flex; align-items: center;
    height: 35.5px; font-size: 24px; color: var(--text-dark);
  }
  .contact-list svg { width: 18px; height: 18px; margin-right: 10px; flex: none; }

  .wave { position: absolute; left: 0; top: 0; width: 840px; height: 482px; }
  .holder {
    position: absolute; right: 56px; top: 430px;
    color: #fff; font-size: 31px; font-weight: 700;
  }
  .holder .title { font-weight: 400; font-size: 26px; letter-spacing: 2px; }

  .mark-circle {
    position: absolute; left: 282px; top: 26px;
    width: 280px; height: 280px; border-radius: 50%;
    background: linear-gradient(#9a9a9a, #555555);
  }
  .entity {
    position: absolute; left: 0; width: 100%; top: 364px;
    text-align: center; color: var(--text-grey);
    font-size: 21.5px; line-height: 30px; letter-spacing: 0.3px;
  }
  .web {
    position: absolute; left: 0; width: 100%; top: 433px;
    text-align: center; color: var(--text-dark);
    font-size: 30px; letter-spacing: 2px;
  }
  .web strong { color: var(--brand-red); font-weight: 700; }
</style>
</head>
<body>

<section class="card card-front">
  <div class="brand-square"></div>
  <div class="brand-name">Brell<br>Haulage<br>Contracting</div>

  <ul class="contact-list">
    <li><svg viewBox="0 0 20 20"><circle cx="10" cy="10" r="8.5" fill="none" stroke="#b0141c" stroke-width="1.6"/><path d="M7 5c-1 1-1 3 1 6s4 4 5 3l1-1-2-2-1 1c-1-.5-2-2-2.5-3l1-1-1.5-2z" fill="#b0141c"/></svg>08 9352 7140</li>
    <li><svg viewBox="0 0 20 20"><rect x="2" y="5" width="16" height="11" fill="#b0141c"/><path d="M2 5l8 6 8-6" fill="none" stroke="#fff" stroke-width="1.4"/></svg>brellhaul@mailbox-example.com.au</li>
    <li><svg viewBox="0 0 20 20"><g fill="none" stroke="#b0141c" stroke-width="1.4"><circle cx="10" cy="10" r="8"/><ellipse cx="10" cy="10" rx="3.5" ry="8"/><path d="M2 10h16M3.5 6h13M3.5 14h13"/></g></svg>www.brellhaul.com</li>
    <li><svg viewBox="0 0 20 20"><path d="M10 2L1 10h3v8h4v-5h4v5h4v-8h3z" fill="#b0141c"/></svg>P.O Box 817 Wattlegrove WA, 6958</li>
  </ul>

  <svg class="wave" viewBox="0 0 840 482" aria-hidden="true">
    <defs>
      <linearGradient id="redBand" x1="0" x2="1">
        <stop offset="0" stop-color="#7a0008"/>
        <stop offset="0.55" stop-color="#e01b24"/>
        <stop offset="1" stop-color="#7a0008"/>
      </linearGradient>
      <linearGradient id="silverLine" x1="0" x2="1">
        <stop offset="0" stop-color="#bdbdbd"/>
        <stop offset="0.5" stop-color="#f2f2f2"/>
        <stop offset="1" stop-color="#a8a8a8"/>
      </linearGradient>
    </defs>
    <path d="M0,318 C120,420 260,462 400,442 C560,420 700,378 840,376 L840,482 L0,482 Z" fill="url(#redBand)"/>
    <path d="M0,290 C110,400 250,452 390,442" fill="none" stroke="url(#silverLine)" stroke-width="6"/>
    <path d="M620,392 C700,376 780,368 840,364" fill="none" stroke="url(#silverLine)" stroke-width="6"/>
  </svg>

  <div class="holder">Your Name &nbsp;/&nbsp; <span class="title">Title</span></div>
</section>

<section class="card card-back">
  <div class="mark-circle"></div>
  <p class="entity">Brell Holdings Pty Ltd (ACN 582 316 907)<br>ATF The Brell Discretionary Trust T/AS</p>
  <p class="web">www.<strong>brellhaul</strong>.com</p>
</section>

</body>
</html>
```